Car show marketing A5 one sided leaflet/brochure

We are a car enthusiast group that is hosting a performance vehicle trade show & show and shine event. We require a Brochure/leaflet advertising this trade show . Not folded. Just one sided A5 leaflet. We were liking the look of car headlights (but for the car make/model to be non-descript) just that it is an actual car ... Moody ... there will be a DJ playing and arcade racing etc. so that type of 'electronic' fun, motor enthuiast feel. Plus in the background or somewhere on it have the hall in which we are hosting it. I have attached a photo of the hall. The expo is called "Chrome Tide Showcase" being hosted by "Vantor Speedworks" The catchfrase is "Forging Roadway Kinship" I have also attached the vantor speedworks logo. It will be at the "The Marlowe Pavilion" Brisbane on 9th March 2024 from 9.30am to 5pm. It will be showcasing automotive businesses. Please have somewhere on the brochure there will be live entertainment and kids entertainment. Catering throughout the event. (Food stalls & cafe). Entry just $25 - kids under 12 free. See website for details. www.vantorspeedworks.com.au *** I have attached a picture of a idea we had thrown together but obviously we are not in any way able to put together the flyer as we have no experience. We are open for any other design ideas. Thank you!!

Target Market(s)

Car Enthusiasts & families

Industry/Entity Type

Motor

Font styles to use
Serif
Other font styles liked:
• Car racing font such as outrider for example only

Requirements
Must have
• Car feel

```html
<!DOCTYPE html>
<html lang="en">
<head>
<meta charset="utf-8">
<title>Chrome Tide Showcase — Leaflet</title>
<link rel="stylesheet" href="https://fonts.googleapis.com/css2?family=Audiowide&family=Kanit:ital,wght@1,500;1,800;1,900&display=swap">
<style>
  :root {
    --paper: #ffffff;
    --signal-red: #e3342a;
    --deep-red: #c52117;
    --ink: #231f20;
    --wall-blue: #6f8aa3;
    --wall-teal: #79b7b0;
    --asphalt: #9aa3a6;
  }
  * { margin: 0; padding: 0; box-sizing: border-box; }
  html, body { width: 846px; height: 1200px; overflow: hidden; background: var(--paper); }
  .leaflet { position: relative; width: 846px; height: 1200px; overflow: hidden; background: var(--paper); }

  .event-details {
    position: absolute; top: 56px; left: 0; width: 846px;
    text-align: center; color: var(--signal-red);
    font-family: "Audiowide", sans-serif; font-size: 21px; line-height: 32px;
    letter-spacing: 1px; transform: skewX(-10deg);
  }

  .hero-photo { position: absolute; inset: 0; }

  .tagline-band {
    position: absolute; top: 458px; left: 45px; width: 760px; height: 50px;
    background: var(--signal-red); filter: blur(6px); opacity: .9;
  }
  .tagline {
    position: absolute; top: 456px; left: 0; width: 846px; text-align: center;
    color: var(--paper); font-family: "Kanit", sans-serif; font-style: italic; font-weight: 900;
    font-size: 40px; line-height: 52px; letter-spacing: 1px;
  }

  .title-band { position: absolute; background: var(--paper); }
  .title-band--first { top: 525px; left: 0; width: 785px; height: 80px; clip-path: polygon(0 0,100% 0,98% 100%,0 100%); }
  .title-band--second { top: 608px; left: 225px; width: 621px; height: 76px; }
  .title-word {
    position: absolute; color: var(--ink); font-family: "Kanit", sans-serif;
    font-style: italic; font-weight: 900; text-transform: uppercase; letter-spacing: 1px;
  }
  .title-word--first { top: 518px; left: 73px; width: 700px; text-align: center; font-size: 88px; line-height: 92px; }
  .title-word--second { top: 600px; left: 245px; font-size: 88px; line-height: 92px; }

  .speed-lines { position: absolute; }
  .speed-lines span { display: block; height: 6px; background: var(--ink); margin-bottom: 8px; }
  .speed-lines--left { top: 545px; left: 0; width: 60px; }
  .speed-lines--right { top: 632px; left: 556px; width: 290px; }

  .title-badge {
    position: absolute; top: 684px; left: 382px; width: 282px; height: 84px;
    background: var(--signal-red);
  }
  .title-badge-word {
    position: absolute; top: 681px; left: 382px; width: 282px; text-align: center;
    color: var(--ink); font-family: "Kanit", sans-serif; font-style: italic; font-weight: 900;
    font-size: 60px; line-height: 90px;
  }

  .host-name {
    position: absolute; top: 778px; left: 400px; width: 240px; text-align: center;
    color: var(--paper); font-family: "Kanit", sans-serif; font-style: italic; font-weight: 800;
    font-size: 17px; letter-spacing: 2px; text-transform: uppercase;
  }

  .entry-panel {
    position: absolute; top: 1002px; left: 0; width: 330px; height: 198px;
    background: var(--signal-red); clip-path: polygon(0 0,100% 0,89% 100%,0 100%);
  }
  .entry-text {
    position: absolute; top: 1020px; left: 10px; width: 300px; text-align: center; color: var(--paper);
    font-family: "Kanit", sans-serif; font-style: italic;
  }
  .entry-label { font-weight: 900; font-size: 33px; line-height: 36px; letter-spacing: 1px; }
  .entry-price { font-weight: 900; font-size: 74px; line-height: 70px; }
  .entry-note { font-family: "Audiowide", sans-serif; font-style: normal; transform: skewX(-10deg); font-size: 19px; line-height: 26px; margin-top: 6px; }

  .extras {
    position: absolute; top: 1060px; left: 380px; width: 420px; text-align: right;
    color: var(--signal-red); font-family: "Audiowide", sans-serif; font-size: 21px; line-height: 30px;
    transform: skewX(-10deg);
  }
</style>
</head>
<body>
<main class="leaflet">
  <p class="event-details">ON 9TH MARCH 2024 FROM 9.30AM TO 5PM<br>AT "THE MARLOWE PAVILION" BRISBANE</p>

  <svg class="hero-photo" width="846" height="1200" viewBox="0 0 846 1200" role="img" aria-label="Close-up photo of a red sports car front with headlight, beside a colourful striped mural wall">
    <defs>
      <linearGradient id="car-to-wall" x1="0" y1="0" x2="1" y2="0">
        <stop offset="0" stop-color="#c8301c"/>
        <stop offset=".42" stop-color="#b8321f"/>
        <stop offset=".58" stop-color="#3b3d44"/>
        <stop offset=".75" stop-color="#6f8aa3"/>
        <stop offset="1" stop-color="#b27a86"/>
      </linearGradient>
      <linearGradient id="ground-shade" x1="0" y1="0" x2="0" y2="1">
        <stop offset="0" stop-color="#000" stop-opacity="0"/>
        <stop offset=".55" stop-color="#000" stop-opacity=".05"/>
        <stop offset="1" stop-color="#1a1a1a" stop-opacity=".35"/>
      </linearGradient>
      <linearGradient id="top-fade" x1="0" y1="0" x2="0" y2="1">
        <stop offset="0" stop-color="#fff" stop-opacity=".95"/>
        <stop offset="1" stop-color="#fff" stop-opacity="0"/>
      </linearGradient>
    </defs>
    <path d="M0 215 Q 400 125 846 135 L846 880 Q 620 1010 330 1040 L0 1045 Z" fill="url(#car-to-wall)"/>
    <path d="M0 215 Q 400 125 846 135 L846 880 Q 620 1010 330 1040 L0 1045 Z" fill="url(#ground-shade)"/>
    <rect x="0" y="0" width="200" height="260" fill="url(#top-fade)"/>
  </svg>

  <div class="tagline-band"></div>
  <p class="tagline">FORGING ROADWAY KINSHIP</p>

  <div class="title-band title-band--first"></div>
  <div class="title-band title-band--second"></div>
  <div class="speed-lines speed-lines--left"><span></span><span></span><span></span></div>
  <h1>
    <span class="title-word title-word--first">CHROME</span>
    <span class="title-word title-word--second">TIDE</span>
    <span class="title-badge"></span>
    <span class="title-badge-word">SHOWCASE</span>
  </h1>
  <div class="speed-lines speed-lines--right"><span></span><span></span><span></span></div>

  <p class="host-name">Vantor Speedworks</p>

  <div class="entry-panel"></div>
  <div class="entry-text">
    <p class="entry-label">ENTRY JUST</p>
    <p class="entry-price">$25</p>
    <p class="entry-note">FREE FOR KIDS<br>UNDER 12</p>
  </div>

  <p class="extras">AND THERE WILL BE MANY<br>LIVE ENTERTAINMENT AND<br>KIDS EVENTS TOO!</p>
</main>
</body>
</html>
```